Realtor branding business card

modern, simple and self branding. Broker office logo needs to be used but not emphasized. Looking to brand myself

Target Market(s)

buyers, sellers and investors

Industry/Entity Type

Realtor

Contact Information for Business Card

Sample of my current business card on file

Requirements
Must have
• my website - tobiasmerrowkl.com
• Realtor logo
• Fair housing logo
Nice to have
• Colors from office logo but not a must
Should not have
• Do not want headshot

```html
<!DOCTYPE html>
<html lang="en">
<head>
<meta charset="utf-8">
<title>Tobias Merrow – Business Card</title>
<link rel="stylesheet" href="https://fonts.googleapis.com/css2?family=Oswald:wght@600;700&family=Lato:wght@400&display=swap">
<style>
  :root {
    --page-bg: #e9e7e3;
    --card-white: #ffffff;
    --card-black: #262626;
    --navy: #2a2a6e;
    --red: #c0272d;
    --blue: #2f6fbf;
    --ink: #2b2b2b;
    --badge: #c9ccd3;
    --white: #ffffff;
  }
  * { margin: 0; padding: 0; box-sizing: border-box; }
  html, body {
    width: 1200px; height: 1200px; overflow: hidden;
    background: var(--page-bg);
  }
  .canvas {
    width: 1200px; height: 1200px;
    display: flex; flex-direction: column;
    align-items: center; justify-content: center; gap: 34px;
  }
  .card {
    width: 960px; height: 549px;
    border-radius: 4px;
    box-shadow: 0 6px 18px rgba(0,0,0,.15);
    position: relative; overflow: hidden;
  }

  /* Back */
  .card--back {
    background: var(--card-black);
    display: flex; align-items: center; justify-content: center;
  }
  .brand-back {
    font-family: "Oswald", sans-serif; font-weight: 700;
    color: var(--white); line-height: 1.05;
    display: flex; align-items: center; gap: 18px;
  }
  .brand-back .mark { width: 24px; height: 24px; background: var(--white); flex: none; }
  .brand-back .name { display: block; font-size: 56px; text-transform: uppercase; letter-spacing: 1px; }
  .brand-back .sub { display: block; font-size: 56px; text-transform: uppercase; letter-spacing: 1px; }

  /* Front */
  .card--front {
    background: var(--card-white);
    display: flex; align-items: center;
  }
  .brand-front {
    width: 440px; padding-left: 90px;
    font-family: "Oswald", sans-serif; font-weight: 700;
    color: var(--navy); line-height: 1.05;
    display: flex; align-items: center; gap: 14px;
  }
  .brand-front .mark { width: 18px; height: 18px; border-radius: 50%; background: var(--navy); flex: none; }
  .brand-front .name,
  .brand-front .sub { display: block; font-size: 40px; text-transform: uppercase; letter-spacing: 1px; }
  .divider {
    width: 2px; height: 230px; background: var(--red);
    margin-left: 40px; margin-right: 58px; flex: none;
  }
  .contact { font-family: "Lato", sans-serif; color: var(--ink); }
  .contact .agent-name {
    font-family: "Oswald", sans-serif; font-weight: 600;
    font-size: 38px; text-transform: uppercase; letter-spacing: .5px; line-height: 1.1;
  }
  .contact .agent-title { color: var(--blue); font-size: 25px; margin-bottom: 10px; }
  .contact-list { list-style: none; font-size: 21px; line-height: 1.4; }
  .contact-list li { display: flex; align-items: center; gap: 10px; white-space: nowrap; }
  .contact-list svg { width: 18px; height: 18px; fill: var(--blue); flex: none; }
  .contact .address { font-size: 21px; line-height: 1.4; }

  .badges {
    position: absolute; left: 90px; bottom: 44px;
    display: flex; gap: 16px;
  }
  .badge { width: 44px; height: 44px; background: var(--badge); border-radius: 4px; }
</style>
</head>
<body>
<main class="canvas">
  <section class="card card--back" aria-label="Card back">
    <div class="brand-back">
      <span class="mark"></span>
      <div><span class="name">Brightfield</span><span class="sub">Realty Group</span></div>
    </div>
  </section>

  <section class="card card--front" aria-label="Card front">
    <div class="brand-front">
      <span class="mark"></span>
      <div><span class="name">Brightfield</span><span class="sub">Realty Group</span></div>
    </div>
    <div class="divider"></div>
    <div class="contact">
      <h1 class="agent-name">Tobias Merrow</h1>
      <p class="agent-title">Realtor</p>
      <ul class="contact-list">
        <li><svg viewBox="0 0 24 24" aria-hidden="true"><path d="M6.6 10.8a15 15 0 0 0 6.6 6.6l2.2-2.2a1 1 0 0 1 1-.25 11.4 11.4 0 0 0 3.6.57 1 1 0 0 1 1 1V20a1 1 0 0 1-1 1A17 17 0 0 1 3 4a1 1 0 0 1 1-1h3.5a1 1 0 0 1 1 1c0 1.25.2 2.45.57 3.6a1 1 0 0 1-.25 1z"/></svg>Cell:&nbsp; +407 - 555 - 0147</li>
        <li><svg viewBox="0 0 24 24" aria-hidden="true"><path d="M2 8c0-2 5-4 10-4s10 2 10 4v2h-5V8H7v2H2zM6 12h12l2 8H4z"/></svg>Office:&nbsp; +407 - 555 - 0182</li>
        <li><svg viewBox="0 0 24 24" aria-hidden="true"><path d="M2 5h20v14H2zM4 7v.5l8 5.5 8-5.5V7z"/></svg>tmerrow@tobiasmerrowkl.com</li>
        <li><svg viewBox="0 0 24 24" aria-hidden="true"><path d="M12 2a10 10 0 1 0 0 20 10 10 0 0 0 0-20zm0 2c.9 0 2.2 2 2.7 5H9.3C9.8 6 11.1 4 12 4zM4.3 11h4.8c0 .7 0 1.3.1 2H4.3a8 8 0 0 1 0-2zm10.6 0h4.8a8 8 0 0 1 0 2h-4.9c.1-.7.1-1.3.1-2zM9.3 15h5.4c-.5 3-1.8 5-2.7 5s-2.2-2-2.7-5z"/></svg>www.tobiasmerrowkl.com</li>
      </ul>
      <p class="address">480 Linden Grove<br>Dr. Maple Hollow, FL 32000</p>
    </div>
    <div class="badges">
      <span class="badge" role="img" aria-label="Realtor association badge"></span>
      <span class="badge" role="img" aria-label="Equal housing opportunity badge"></span>
    </div>
  </section>
</main>
</body>
</html>
```